Business Card Design For Marketing Agnecy LVP

Need business card design for marketing agency.

Doug Fenwick
President, CEO
1-555-302-4196
doug@boldpromoperksgroup.example
www.BoldPromoPerksGroup.example

Back Side:
Boost Sales Using Rewards, Incentives & Giveaways
Get A Free Sample Package

Target Market(s)

B2B

Industry/Entity Type

Marketing

Contact Information for Business Card

Doug Fenwick
President, CEO
1-555-302-4196

Back Side:
Get A Free Sample Package

Please note that my current url is OLD DESIGN. I am working on new design and want the business card to match color themes at least on new site. Here is the demo link for new site so you can see the colors I use, etc.

http://layoutcratehub.example/kq/doug/lvp_final/index.html

Requirements
Must have
• Please note that my current url is OLD DESIGN. I am working on new design and want the business card to match color themes at least on new site. Here is the demo link for new site so you can see the colors I use, etc.

Nice to have

Should not have

```html
<!DOCTYPE html>
<html lang="en">
<head>
<meta charset="utf-8">
<title>LVP Business Card – Front and Back</title>
<link href="https://fonts.googleapis.com/css2?family=Montserrat:wght@400;500;700;800&family=Mulish:wght@400;600&display=swap" rel="stylesheet">
<style>
  :root {
    --bg: #d3d8da;
    --paper: #f2f2ef;
    --brand-blue: #1b75c4;
    --edge-blue: #1658b0;
    --ink: #5a5c60;
    --ink-soft: #7b7d80;
    --white: #ffffff;
  }
  * { box-sizing: border-box; margin: 0; padding: 0; }
  html, body {
    width: 1200px; height: 852px; overflow: hidden;
    background: var(--bg);
    font-family: "Mulish", sans-serif;
  }
  .sheet {
    width: 1200px; height: 852px;
    display: flex; flex-direction: column; align-items: center; justify-content: center;
    gap: 28px;
  }
  .card {
    width: 680px; height: 388px;
    background: var(--paper);
    border-bottom: 5px solid var(--edge-blue);
    box-shadow: 0 6px 18px rgba(0,0,0,0.12);
    position: relative;
  }

  /* Front */
  .card-front { display: flex; align-items: center; padding: 0 56px; }
  .brand-block {
    width: 230px; display: flex; align-items: center; gap: 10px;
  }
  .brand-name {
    font-family: "Montserrat", sans-serif; font-weight: 800;
    color: var(--brand-blue); font-size: 30px; line-height: 1.05;
    text-transform: uppercase; letter-spacing: 0.5px;
  }
  .brand-dot {
    width: 14px; height: 14px; border-radius: 50%;
    background: var(--brand-blue); align-self: flex-start; margin-top: 4px;
  }
  .divider {
    width: 2px; height: 190px; background: var(--brand-blue);
    margin: 0 34px 0 22px;
  }
  .contact-block { flex: 1; }
  .person-name {
    font-family: "Montserrat", sans-serif; font-weight: 700;
    color: var(--brand-blue); font-size: 25px; letter-spacing: 1px;
    text-transform: uppercase;
  }
  .person-title { color: var(--ink); font-size: 18px; margin: 4px 0 16px; }
  .contact-list { list-style: none; }
  .contact-list li {
    display: flex; align-items: center; gap: 10px;
    color: var(--ink); font-size: 16px; line-height: 1.7;
  }
  .contact-list svg { width: 15px; height: 15px; flex: none; }

  /* Back */
  .card-back {
    display: flex; flex-direction: column; align-items: center; justify-content: center;
    padding: 0 48px;
  }
  .back-brand {
    font-family: "Montserrat", sans-serif; font-weight: 800;
    color: var(--brand-blue); font-size: 40px; letter-spacing: 1px;
    text-transform: uppercase;
  }
  .tagline {
    color: var(--ink-soft); font-family: "Montserrat", sans-serif; font-weight: 500;
    font-size: 17px; letter-spacing: 0.6px; margin: 18px 0 20px;
  }
  .cta {
    width: 100%; background: var(--brand-blue); color: var(--white);
    border-radius: 6px; text-align: center; padding: 22px 0;
    font-family: "Montserrat", sans-serif; font-weight: 800;
    font-size: 24px; letter-spacing: 2px; text-transform: uppercase;
  }
  .back-url { color: var(--ink); font-size: 17px; margin-top: 22px; letter-spacing: 0.4px; }
</style>
</head>
<body>
<main class="sheet">
  <section class="card card-front" aria-label="Business card front">
    <div class="brand-block">
      <p class="brand-name">Bold Promo Perks Group</p>
      <span class="brand-dot"></span>
    </div>
    <div class="divider"></div>
    <div class="contact-block">
      <h1 class="person-name">Doug Fenwick</h1>
      <p class="person-title">President, CEO</p>
      <ul class="contact-list">
        <li>
          <svg viewBox="0 0 16 16" aria-hidden="true"><path d="M4 1.5l2.2 3-1.3 1.6c.8 1.9 2.2 3.3 4.1 4.1l1.6-1.3 3 2.2-1.2 2.4C7.3 13.3 2.7 8.7 1.6 3.7z" fill="none" stroke="#1b75c4" stroke-width="1.5" stroke-linejoin="round"/></svg>
          <span>1-555-302-4196</span>
        </li>
        <li>
          <svg viewBox="0 0 16 16" aria-hidden="true"><rect x="1.5" y="3.5" width="13" height="9" fill="none" stroke="#1b75c4" stroke-width="1.5"/><path d="M1.5 3.5L8 9l6.5-5.5" fill="none" stroke="#1b75c4" stroke-width="1.5"/></svg>
          <span>doug@boldpromoperksgroup.example</span>
        </li>
        <li>
          <svg viewBox="0 0 16 16" aria-hidden="true"><circle cx="8" cy="8" r="6.5" fill="none" stroke="#1b75c4" stroke-width="1.4"/><ellipse cx="8" cy="8" rx="2.8" ry="6.5" fill="none" stroke="#1b75c4" stroke-width="1.2"/><path d="M1.5 8h13" stroke="#1b75c4" stroke-width="1.2"/></svg>
          <span>www.BoldPromoPerksGroup.example</span>
        </li>
      </ul>
    </div>
  </section>

  <section class="card card-back" aria-label="Business card back">
    <p class="back-brand">Bold Promo Perks Group</p>
    <p class="tagline">Boost Sales Using Rewards, Incentives &amp; Giveaways</p>
    <p class="cta">Get A Free Sample Package</p>
    <p class="back-url">www.BoldPromoPerksGroup.example</p>
  </section>
</main>
</body>
</html>
```